PostCard Design Project

I am making a mailing postcard
I am having the mailing printed using 4 color foil on certain parts.
I am looking for a design that maximizes the foil process where certain parts are done in foil to grab the customers attention (example: if there is a car on the postcard the headlights would be done in foil) .
I am targeting some industries, (auto, real estate, medical, beauty) I would like the post card to have examples of postcard ideas for 2 or 3 of these industries.
specs:
the postcard should be atleast 6.5x9 up to 8.5x11, I don't want to restrict the space for the creative as I don't want everything to look like a huge mess. both sides will be used.
the piece is a direct mail piece so it has to meet requirements of https://www.mailvantor.com/business/pdf/quick-reference-guide.pdf
text will be
"business with no limits, meet mailing with no addresses, gain new customers through "Open Porch Route Drop" reach new customers at their home without needing their address. "
I also want some current print specials I am running included.
-double your order FREE (order 500 business cards and get 1000)
-250 100lb gloss stock brochures 99.00
-business packages (cards, envelopes and letterhead) 299
-1000 flyers 140.40
-5000 postcards 179.99
A list of services
banners
booklets
brochures
business cards
calendars
catalogs
CD/DVD packages
envelopes
event tickets
flyers
hangtags
postcards
posters
presentation folders
rack cards
labels
table tents
window cling and decal
"order 24/7 orders@inkwillow.com" must be included
my logo is InkWillow will be supplied later
ive received some great designs. however Im looking for something a little more modern like some zorvel would put out. if the amount of words is too much please feel free to edit. also an idea i had for the list of services i offer is to have it transparent yet readable as the background of the postcard some small some big but covering the entire backgroud. you can then design on top of that with other thing. just an early morning thought
Reason: I have uploaded a sketch of my idea, please take time to look at it for an accurate depiction of what im looking for. feel free to add elements that make it pop off the page
Reason: We are getting close i will be providing feed back today

```html
<!DOCTYPE html>
<html lang="en">
<head>
<meta charset="utf-8">
<title>InkWillow Direct Mail Postcard</title>
<link rel="stylesheet" href="https://fonts.googleapis.com/css2?family=Arimo:wght@400;700&display=swap">
<style>
  :root {
    --navy: #0e1a2c;
    --ink: #050a12;
    --cyan: #22a9df;
    --lime: #9fcb3b;
    --lime-light: #b6d94a;
    --grey-word: #a3a3a3;
    --paper: #ffffff;
    --stage: #e9e7e3;
    --bullet-ink: #15202e;
  }
  * { box-sizing: border-box; margin: 0; padding: 0; }
  html, body { width: 1200px; height: 1000px; overflow: hidden; }
  body {
    background: var(--stage);
    font-family: "Arimo", Arial, sans-serif;
    position: relative;
  }
  .postcard {
    position: absolute;
    left: 200px;
    width: 800px;
    height: 470px;
    overflow: hidden;
    box-shadow: 0 6px 18px rgba(0,0,0,.18);
  }
  .postcard--front { top: 22px; background: var(--navy); }
  .postcard--back { top: 510px; background: var(--paper); }

  .band-art { position: absolute; inset: 0; width: 800px; height: 470px; }

  /* front */
  .headline {
    position: absolute;
    top: 30px; left: 10px; right: 10px;
    text-align: center;
    color: var(--cyan);
    font-weight: 700;
    font-size: 21px;
    line-height: 1.3;
  }
  .headline span { display: block; white-space: nowrap; }
  .collage {
    position: absolute;
    left: 70px; top: 185px;
    width: 300px; height: 210px;
    transform: rotate(-8deg);
    background: linear-gradient(135deg, #e9f3fa 0%, #5fb7e4 35%, #f0c03a 65%, #e2583e 100%);
    border-radius: 4px;
    box-shadow: 0 4px 10px rgba(0,0,0,.3);
  }
  .mini-stack {
    position: absolute;
    left: 708px; top: 160px;
    width: 78px; height: 110px;
    transform: rotate(-6deg);
    background: linear-gradient(160deg, #ffffff 0%, #f3d9cf 45%, #d8342f 100%);
    box-shadow: 0 3px 8px rgba(0,0,0,.25);
  }
  .specials {
    position: absolute;
    left: 410px; top: 190px;
    width: 290px;
    list-style: none;
    color: var(--bullet-ink);
    font-size: 14px;
    line-height: 1.45;
  }
  .specials li { padding-left: 16px; position: relative; }
  .specials li::before {
    content: ""; position: absolute; left: 0; top: 6px;
    width: 8px; height: 8px; border-radius: 50%; background: var(--bullet-ink);
  }
  .order-line {
    position: absolute;
    left: 30px; bottom: 18px;
    color: var(--lime);
    font-weight: 700;
    font-size: 24px;
    white-space: nowrap;
  }

  /* back */
  .service-wall {
    position: absolute;
    top: -4px; left: -40px;
    width: 900px;
    font-weight: 700;
    white-space: nowrap;
  }
  .service-row { font-size: 23px; line-height: 29px; color: var(--grey-word); }
  .service-row--accent { font-size: 25px; }
  .lime { color: var(--lime); }
  .cyan { color: var(--cyan); }
  .postage-box {
    position: absolute;
    left: 566px; top: 28px;
    width: 78px; height: 58px;
    border: 1px solid #333;
    background: var(--paper);
    font-size: 12px; color: #222;
    display: flex; align-items: center; justify-content: center;
    text-align: center; line-height: 1.2;
  }
  .showcase {
    position: absolute;
    border-radius: 50%;
    border: 6px solid var(--lime-light);
    background: var(--paper);
    padding: 5px;
  }
  .showcase-ring {
    width: 100%; height: 100%;
    border-radius: 50%;
    border: 6px solid var(--cyan);
    padding: 4px;
    background: var(--paper);
  }
  .showcase-photo { width: 100%; height: 100%; border-radius: 50%; }
  .showcase--brochure { left: 650px; top: 30px; width: 140px; height: 140px; }
  .showcase--brochure .showcase-photo { background: linear-gradient(135deg, #f4f7f7, #9fcfc0 60%, #4d8fa8); }
  .showcase--folder { left: 690px; top: 165px; width: 120px; height: 120px; }
  .showcase--folder .showcase-photo { background: linear-gradient(135deg, #f4e34a, #e6cf12 60%, #333); }
  .showcase--print { left: 570px; top: 185px; width: 100px; height: 100px; }
  .showcase--print .showcase-photo { background: linear-gradient(135deg, #c9d9ee, #4a6fa8 60%, #1e2f55); }
</style>
</head>
<body>

<section class="postcard postcard--front" aria-label="Postcard front">
  <svg class="band-art" viewBox="0 0 800 470" aria-hidden="true">
    <path d="M0,176 Q400,130 800,112 L800,124 Q400,142 0,190 Z" fill="var(--ink)"/>
    <path d="M0,190 Q400,142 800,124 L800,136 Q400,154 0,202 Z" fill="var(--cyan)"/>
    <path d="M0,202 Q400,154 800,136 L800,350 Q400,362 0,392 Z" fill="var(--lime)"/>
    <path d="M0,392 Q400,362 800,350 L800,362 Q400,374 0,404 Z" fill="var(--ink)"/>
    <path d="M0,404 Q400,374 800,362 L800,374 Q400,386 0,416 Z" fill="var(--cyan)"/>
  </svg>

  <p class="headline"><span>“ Business with no limits, meet mailing with no addresses,</span><span>Gain new customers through "Open Porch Route Drop"</span><span>Reach new customers at their home without needing their address. ”</span></p>

  <div class="collage" role="img" aria-label="Fanned stack of sample printed flyers and brochures"></div>
  <div class="mini-stack" role="img" aria-label="Small stack of sample brochures and envelopes"></div>

  <ul class="specials">
    <li>Double your order FREE<br>(order 500 business cards and get 1000)</li>
    <li>250 100lb gloss stock brochures 99.00</li>
    <li>Business packages<br>(cards, envelopes and letterhead) 299</li>
    <li>1000 flyers 140.40</li>
    <li>5000 postcards 179.99</li>
  </ul>

  <p class="order-line">order 24/7 orders@inkwillow.com</p>
</section>

<section class="postcard postcard--back" aria-label="Postcard back">
  <div class="service-wall" aria-label="Services offered">
    <p class="service-row">ners • banners • booklets • brochures</p>
    <p class="service-row service-row--accent"><span class="lime">• banners</span> • <span class="cyan">booklets</span> • <span class="lime">brochures</span></p>
    <p class="service-row">klets • brochures • business cards • calendars</p>
    <p class="service-row service-row--accent">ds • <span class="lime">calendars</span> • <span class="cyan">catalogs</span> • <span class="lime">CD/DVD</span></p>
    <p class="service-row">ndars • catalogs • <span class="cyan">envelopes</span> • <span class="lime">event tickets</span></p>
    <p class="service-row">ogs • CD/DVD packages • <span class="cyan">flyers</span> • <span class="lime">hangtags</span></p>
    <p class="service-row">packages • envelopes • <span class="cyan">postcards</span> • posters</p>
    <p class="service-row">lopes • <span class="lime">posters</span> • <span class="cyan">presentation folders</span></p>
    <p class="service-row">tickets • hangtags • <span class="lime">rack cards</span> • labels</p>
    <p class="service-row">angtags • posters • presentation folders • <span class="cyan">labels</span> • <span class="lime">table tents</span></p>
    <p class="service-row">ack cards • labels • table tents • <span class="cyan">window cling and decal</span></p>
    <p class="service-row">ls • table tents</p>
  </div>

  <svg class="band-art" viewBox="0 0 800 470" aria-hidden="true">
    <path d="M0,394 Q400,384 800,308 L800,318 Q400,394 0,404 Z" fill="var(--lime)"/>
    <path d="M0,404 Q400,394 800,318 L800,332 Q400,408 0,418 Z" fill="var(--cyan)"/>
    <path d="M0,418 Q400,408 800,332 L800,470 L0,470 Z" fill="var(--navy)"/>
  </svg>

  <div class="postage-box">Postage<br>Stamp</div>

  <div class="showcase showcase--brochure"><div class="showcase-ring"><div class="showcase-photo" role="img" aria-label="Sample tri-fold brochure"></div></div></div>
  <div class="showcase showcase--print"><div class="showcase-ring"><div class="showcase-photo" role="img" aria-label="Sample printed brochure spread"></div></div></div>
  <div class="showcase showcase--folder"><div class="showcase-ring"><div class="showcase-photo" role="img" aria-label="Sample yellow presentation folder"></div></div></div>

  <p class="order-line">order 24/7 orders@inkwillow.com</p>
</section>

</body>
</html>
```